We are a doctors medical practice
I need the business card to be eye catching and memorable,
to reflect professionalism, yet also warmth and care

the numbers need to be easy to see, for the elderly

and the logo also in a location that is large enough to see and be eye catching

Back of card:
opening hours:
Mon- Fri 8.30am to 6pm
Sat 9am to 4pm

rows for appontments, date and time
Updates

HiĀ 

Modification to company name

BROOKVALE KINDRED HEALTH MEDICAL PRACTICE

Thanks
Marla

Reason: I am look for a unique design that also fulfils the design brief

I have attempted to post a .eps and .ai file of the logo

Target Market(s)

needs to appeal to the majority, mainly adults

Industry/Entity Type

Medical

Contact Information for Business Card

company name: Brookvale Kindred Health Medical Practice
Name: Dr Marla Tobrik-Vey
Qualifications: MBBS, Bsci(med), FRACGP, DCH, SH&FPA, Dip Derm
Address: Shop 3/41-43 Corrow St, Kindrel Park 2199
Ph: 02 9184 3025
Fax: 02 9318 6042

Requirements
Nice to have
• I like balance
gold/ silver incorporated, as well as the other colours in the logo- but not limited to these colours
a "medical" feel
Should not have
• dark or strong colours

```html
<!DOCTYPE html>
<html lang="en">
<head>
<meta charset="utf-8">
<title>Brookvale Kindred Health Medical Practice – Business Card</title>
<link rel="stylesheet" href="https://fonts.googleapis.com/css2?family=Cabin+Condensed:wght@400;600;700&family=Open+Sans:wght@400;600&display=swap">
<style>
  :root {
    --bg: #ece9e4;
    --gold: #f1c21a;
    --card-grey: #e4e4e6;
    --card-white: #f3f3f4;
    --brown: #8b6b57;
    --text-grey: #7c7c80;
    --ink: #1c1c1c;
    --accent-blue: #3b9ad6;
  }
  * { box-sizing: border-box; margin: 0; padding: 0; }
  html, body { width: 1200px; height: 900px; overflow: hidden; background: var(--bg); }
  .canvas { position: relative; width: 1200px; height: 900px; }

  .card {
    position: absolute; left: 280px; width: 640px; height: 380px;
    overflow: hidden; box-shadow: 0 6px 18px rgba(0,0,0,0.15);
  }
  .card--front { top: 50px; background: var(--gold); }
  .card--back { top: 470px; background: var(--card-white); }

  .front-swoosh { position: absolute; inset: 0; }

  .doctor-name {
    position: absolute; right: 22px; top: 36px;
    font: 700 32px/1 "Cabin Condensed", sans-serif; color: var(--brown);
  }
  .qualifications {
    position: absolute; right: 22px; top: 82px; text-align: right;
    font: 400 15px/1.45 "Open Sans", sans-serif; color: var(--text-grey);
  }
  .practice-mark {
    position: absolute; left: 48px; top: 110px;
    display: flex; align-items: center; gap: 10px;
    font: 600 18px/1 "Cabin Condensed", sans-serif; color: var(--brown);
  }
  .practice-mark__dot {
    width: 40px; height: 40px; border-radius: 50%;
    border: 4px solid var(--accent-blue); background: #fff;
  }
  .practice-name {
    position: absolute; left: 40px; top: 184px;
    font: 700 27px/1 "Cabin Condensed", sans-serif; color: var(--brown);
    letter-spacing: 0.2px; white-space: nowrap;
  }
  .contact {
    position: absolute; left: 40px; top: 240px;
    display: grid; grid-template-columns: 72px 16px auto; row-gap: 4px;
    font: 400 16px/1.3 "Open Sans", sans-serif; color: var(--text-grey);
  }

  .hours-band {
    position: absolute; left: 0; top: 0; width: 100%; height: 84px;
    background: var(--gold); padding: 14px 26px;
    font: 400 22px/1.2 "Open Sans", sans-serif; color: var(--ink);
  }
  .hours-band__label { font-weight: 600; }
  .hours-band__sat { padding-left: 188px; display: block; }
  .appointments-label {
    position: absolute; left: 26px; top: 96px;
    font: 600 14px/1 "Open Sans", sans-serif; color: var(--ink);
  }
  .appointment-rows { position: absolute; left: 26px; right: 26px; top: 122px; }
  .appointment-row { height: 34px; border-bottom: 2px dotted #555; }
  .date-time-label {
    position: absolute; right: 26px; top: 206px;
    font: 600 14px/1 "Open Sans", sans-serif; color: var(--ink);
  }
</style>
</head>
<body>
<div class="canvas">

  <section class="card card--front">
    <svg class="front-swoosh" width="640" height="380" viewBox="0 0 640 380" aria-hidden="true">
      <path d="M0,150 C150,60 330,40 640,30 L640,215 C560,300 470,350 380,380 L0,380 Z" fill="var(--card-grey)"/>
    </svg>
    <h1 class="doctor-name">Dr Marla Tobrik-Vey</h1>
    <p class="qualifications">MBBS, Bsci(med), FRACGP,<br>DCH, SH&amp;FPA, Dip Derm</p>
    <div class="practice-mark"><span class="practice-mark__dot"></span>Brookvale Kindred Health</div>
    <h2 class="practice-name">BROOKVALE KINDRED HEALTH MEDICAL PRACTICE</h2>
    <div class="contact">
      <span>Tel</span><span>:</span><span>02 9184 3025</span>
      <span>Fax</span><span>:</span><span>02 9318 6042</span>
      <span>Address</span><span>:</span><span>Shop 3/41-43 Corrow St,<br>Kindrel Park 2199</span>
    </div>
  </section>

  <section class="card card--back">
    <div class="hours-band">
      <span class="hours-band__label">OPENING HOURS:</span> Mon– Fri 8.30am to 6pm
      <span class="hours-band__sat">Sat 9am to 4pm</span>
    </div>
    <p class="appointments-label">Appontments</p>
    <div class="appointment-rows">
      <div class="appointment-row"></div>
      <div class="appointment-row"></div>
      <div class="appointment-row"></div>
      <div class="appointment-row"></div>
      <div class="appointment-row"></div>
      <div class="appointment-row"></div>
      <div class="appointment-row"></div>
    </div>
    <p class="date-time-label">Date &amp; Time</p>
  </section>

</div>
</body>
</html>
```